i would like a business card to leave with customers and potential customers for electrical work and for the supply and install of reverse cycle airconditioning in the domestic and commercial market.
I own my own business and im a sole trader. I have an a'class electrical lisence and also a refrigeration lisence so i am
able to offer complete installations in airconditioning by a fully qualified and lisenced tradesman.
im looking for something that comes across as unique and professional.
i had the coluor black and some gold in mind but open to any coluors.
something like Lanterra Electrical & Refrigeration
or Lanterra Air.
i will use this design on a business card to advertise through summer to help generate installs through the busy season.

Target Market(s)

Mainly domestic house holds through summer who are in need of airconditioning and reliable information to acomadate thier cooling and heating requirements

Industry/Entity Type

Electrical

Requirements
Must have
• Business name- Lanterra
My name- Mark Delford
My mobile no- 0438 517 290
My email- mrdelford@qelvo.com.au
Installation & Decomissioning of aiconditioning split systems
LIC NO: TRK 540316
Nice to have
• Lanterra Electrical & Refrigeration

```html
<!DOCTYPE html>
<html lang="en">
<head>
<meta charset="utf-8">
<title>Lanterra Electrical &amp; Refrigeration – Business Card</title>
<link rel="stylesheet" href="https://fonts.googleapis.com/css2?family=Open+Sans:wght@600;700&family=Yellowtail&display=block">
<style>
  :root {
    --gold: #dccb00;
    --black: #0a0a0a;
    --white: #ffffff;
    --backdrop: #e4e6e8;
    --badge-sky: #6fdcf7;
    --badge-lime: #b9f32a;
  }
  * { margin: 0; padding: 0; box-sizing: border-box; }
  html, body {
    width: 1200px; height: 900px; overflow: hidden;
    background: var(--backdrop);
    font-family: "Open Sans", Arial, sans-serif;
  }
  .canvas { position: relative; width: 1200px; height: 900px; }

  .card {
    position: absolute; top: 57px;
    width: 449px; height: 783px;
    border-radius: 22px; overflow: hidden;
  }

  /* Front */
  .card-front { left: 102px; background: var(--gold); color: var(--black); }
  .side-band {
    position: absolute; left: 0; top: 0;
    width: 41px; height: 400px; background: var(--black);
  }
  .email {
    position: absolute; left: 20px; top: 742px;
    transform: rotate(-90deg); transform-origin: left top;
    font-size: 19px; font-weight: 600; letter-spacing: 1px;
    white-space: nowrap;
  }
  .brand-mark {
    position: absolute; left: 128px; top: 66px;
    display: flex; align-items: center; gap: 12px;
    font-size: 34px; font-weight: 700; color: var(--black);
  }
  .brand-mark .square { width: 26px; height: 26px; background: var(--black); }
  .script-name {
    position: absolute; left: 70px; top: 292px;
    width: 370px;
    font-family: "Yellowtail", "Brush Script MT", cursive;
    font-size: 100px; line-height: 1; white-space: nowrap;
  }
  .company {
    position: absolute; left: 210px; top: 415px;
    font-size: 19px; font-weight: 600; line-height: 1.3;
  }
  .person {
    position: absolute; right: 33px; top: 690px; text-align: center;
  }
  .person-name { font-size: 29px; font-weight: 700; letter-spacing: -0.3px; }
  .person-phone { font-size: 20px; font-weight: 700; letter-spacing: 0.5px; margin-top: 4px; }

  /* Back */
  .card-back { left: 650px; background: var(--black); color: var(--white); }
  .service {
    position: absolute; left: 32px; top: 28px;
    font-size: 18px; font-weight: 700; line-height: 1.2;
  }
  .script-vertical {
    position: absolute; left: 232px; top: 780px;
    transform: rotate(-90deg); transform-origin: left top;
    font-family: "Yellowtail", "Brush Script MT", cursive;
    font-size: 200px; line-height: 1; color: var(--gold);
    white-space: nowrap;
  }
  .badge { position: absolute; left: 88px; top: 585px; width: 98px; height: 98px; }
  .licence {
    position: absolute; left: 32px; top: 730px;
    font-size: 19px; font-weight: 700; letter-spacing: 0.3px;
  }
</style>
</head>
<body>
<main class="canvas">
  <section class="card card-front">
    <div class="side-band"></div>
    <p class="email">mrdelford@qelvo.com.au</p>
    <div class="brand-mark"><span class="square"></span><span>Lanterra</span></div>
    <p class="script-name">Lanterra</p>
    <p class="company">Lanterra Electrical<br>&amp; Refrigeration</p>
    <div class="person">
      <p class="person-name">Mark Delford</p>
      <p class="person-phone">0438 517 290</p>
    </div>
  </section>

  <section class="card card-back">
    <p class="service">Installation &amp; Decommissioning<br>of air-conditioning split systems</p>
    <p class="script-vertical">Lanterra</p>
    <svg class="badge" viewBox="0 0 98 98" role="img" aria-label="Authorisation badge">
      <rect width="98" height="49" fill="var(--badge-sky)"/>
      <rect y="49" width="98" height="49" fill="var(--badge-lime)"/>
    </svg>
    <p class="licence">LIC NO: TRK 540316</p>
  </section>
</main>
</body>
</html>
```